Website for a Psychologist in Private Practice

I need a cool web design for my website: www.drkalvoric.com. I would like it to look professional. Keep all the current content and add: Space for video; radio spots (see Silver Cedar Tunes Logo below for those); Quick Inquiry; Friendora link; 5 star rating on Rivo; a map; reviews from former patients. I am open to suggestions.

Target Market(s)

Those seeking individual and marital counseling.

Industry/Entity Type

Mental Health

Number of Pages Required

1 page

Font styles to use
Sans Serif
Other font styles liked:
• I'm open but no hard to read script

Requirements
Must have
• All the content on my home page with link for video and radio spots. List services and degrees and expertices (pics not necessary).
Nice to have
• A video of me and radio conversations (logo of Silver Cedar Tunes radio attached).
Should not have
• Cartoons, comedy, etc.... I don't need pictures of services (marital, depression, etc...) Just list those.

```html
<!DOCTYPE html>
<html lang="en">
<head>
<meta charset="utf-8">
<title>Dr. Mara L. Kalvoric – Clinical Psychologist</title>
<link href="https://fonts.googleapis.com/css2?family=Open+Sans:ital,wght@0,400;0,600;0,700;1,400&family=Playfair+Display:wght@700&display=swap" rel="stylesheet">
<style>
:root{
  --teal:#2a8fa3;
  --ink:#3c3c3c;
  --muted:#6d6d6d;
  --side:#3a3b3d;
  --side-text:#d9d9d9;
  --band:#e6e7e8;
  --footer:#efefef;
  --white:#ffffff;
  --nav:#2b2c2e;
}
*{box-sizing:border-box;margin:0;padding:0}
html,body{width:710px;height:1200px;overflow:hidden;background:var(--white)}
body{position:relative;font-family:"Open Sans",Arial,sans-serif;color:var(--ink);font-size:7px;line-height:1.45}
.hero-bg{position:absolute;left:0;top:0;width:710px;height:650px;background:linear-gradient(135deg,#7fb6c2 0%,#a9cfd2 30%,#d6d7c6 60%,#c9c1ad 100%)}
.site-title{position:absolute;left:20px;top:10px;font-family:"Playfair Display",Georgia,serif;font-size:19px;color:#2f3a40;letter-spacing:.5px}
.tagline{position:absolute;left:20px;top:36px;font-size:6.5px;color:#2f3a40;line-height:1.5}
.main-nav{position:absolute;left:305px;top:0;width:405px;height:22px;background:var(--nav);display:flex;align-items:center;gap:24px;padding-left:16px}
.main-nav a{color:#e0e0e0;text-decoration:none;font-size:6.5px;font-weight:600;letter-spacing:.6px}
.main-nav a.active{color:var(--white);border-bottom:1px solid var(--teal)}
.content-box{position:absolute;left:62px;top:80px;width:410px;height:538px;background:var(--white);padding:26px 22px}
.welcome{font-size:15px;color:var(--teal);font-weight:400;margin-bottom:10px}
.content-box p{margin-bottom:7px;color:var(--muted)}
.content-box h2{font-size:11px;font-weight:700;color:var(--ink);margin:12px 0 7px;letter-spacing:.4px}
.content-box h3{font-size:7px;font-weight:700;color:var(--ink);margin:10px 0 4px}
.sidebar{position:absolute;left:472px;top:24px;width:170px;height:594px;background:var(--side);color:var(--side-text)}
.portrait{width:170px;height:132px;background:linear-gradient(160deg,#6f8fa0,#c9a98a 55%,#e6d2b5)}
.side-inner{padding:12px 14px}
.side-title{font-size:8px;color:#7fc7d4;font-weight:700;letter-spacing:.5px}
.side-sub{font-size:6px;margin-bottom:6px}
.side-rule{width:26px;border-top:1px solid #8a8a8a;margin:6px 0 10px}
.side-list{list-style:none;font-size:6.5px;line-height:1.7}
.side-head{font-size:8px;font-weight:700;color:var(--white);letter-spacing:.6px;margin-top:16px}
.testimonial{position:absolute;left:0;top:650px;width:710px;height:95px;background:var(--band);text-align:center;padding-top:8px}
.avatar{width:34px;height:34px;border-radius:50%;margin:0 auto 6px;background:linear-gradient(135deg,#8a7a6a,#cbb59c)}
.quote{width:430px;margin:0 auto;font-style:italic;color:var(--muted);font-size:6.5px}
.quote-by{margin-top:4px;font-size:6px;color:var(--muted)}
.col{position:absolute;top:755px}
.col h4{font-size:8px;font-weight:700;letter-spacing:.6px;color:var(--ink);margin-bottom:2px}
.col .rule{width:20px;border-top:1px solid var(--teal);margin-bottom:10px}
.videos{left:62px;width:180px}
.video-frame{width:180px;height:112px;background:linear-gradient(120deg,#9fc4c9,#d9c9a8);position:relative}
.video-bar{position:absolute;left:0;bottom:0;width:100%;height:11px;background:#1e1e1e}
.contact{left:270px;width:180px}
.field{width:180px;height:13px;border:1px solid #cfcfcf;margin-bottom:5px;font-size:6px;color:#9a9a9a;padding:2px 5px}
.field.message{height:34px}
.send{display:inline-block;background:var(--teal);color:var(--white);font-size:6px;font-weight:700;padding:3px 12px;letter-spacing:.5px}
.conversations{left:482px;width:160px}
.radio-art{width:160px;height:128px;background:linear-gradient(135deg,#e3a9b6,#f2d7a6 50%,#9cc8e0)}
.site-footer{position:absolute;left:0;top:925px;width:710px;height:95px;background:var(--footer)}
.badge-group{position:absolute;left:70px;top:16px;display:flex;gap:30px}
.badge{width:58px;text-align:center;font-size:5.5px;color:var(--muted)}
.badge-shape{width:58px;height:22px;background:#c9c9c9;margin-top:3px}
.badge-shape.red{background:#b5322c}
.map{position:absolute;left:270px;top:12px;width:180px;height:62px;background:linear-gradient(135deg,#dfe6d9,#e9e4d7)}
.reach{position:absolute;left:505px;top:10px;width:150px;text-align:left}
.socials{display:flex;gap:8px;margin-left:62px;margin-bottom:4px}
.social{display:flex;align-items:center;gap:3px;font-size:6px;font-weight:600;color:var(--teal)}
.social-dot{width:6px;height:6px;background:var(--teal)}
.phone{font-size:17px;color:var(--teal);display:flex;align-items:center;gap:5px}
.address{font-size:6px;color:var(--muted);margin-left:16px;line-height:1.6}
.copyright{position:absolute;left:0;top:1030px;width:710px;text-align:center;font-size:6px;color:var(--muted)}
</style>
</head>
<body>
<div class="hero-bg" role="img" aria-label="Calm ocean water meeting a sandy beach"></div>

<div class="site-title">DR. MARA L. KALVORIC</div>
<div class="tagline">Helping individuals, couples and families find clarity and calm<br>CA License PSY 6817 · Seabright, California</div>

<nav class="main-nav">
  <a class="active" href="#">HOME</a><a href="#">ABOUT</a><a href="#">SERVICES</a><a href="#">RESOURCES</a><a href="#">FAQ</a><a href="#">CONTACT</a>
</nav>

<main class="content-box">
  <h1 class="welcome">I'm so glad you are here.</h1>
  <p>Choosing to see a professional for issues in your life can be difficult but also possibly life changing. Many people are seeking help because they believe asking is a sign of weakness. Failure on their part...</p>
  <p><b>Really? We seek the help of experts all the time (contractors, mechanics, chefs, etc.) and what is more important than your life?</b></p>
  <p>Consulting with a trusted expert to aid in your best interest can be time well spent. So if you are willing to take the time to invest in counseling, make sure that it is with someone that is worth your time.</p>
  <h2>WHY CHOOSE ME</h2>
  <p>Choose a licensed psychologist with a doctoral degree (Ph.D. or Psy.D.). Both have over 14 years of education in the field of psychology, extensive internships and comprehensive licensing exams. Others have far less education if any. Also consider the therapist's approach to therapy. I use a straightforward approach (quantifiable workable open rapport) with brief, solution oriented sessions.</p>
  <p>Experience also separates good psychologists from others with fewer and more proficient sessions. My 30+ years of professional experience and my life experience contributes to the empathetic perspective I use to relate to each person I see. I also believe it is the reason 95% of my practice is referral based and why many other psychologists in the area seek my services.</p>
  <h3>DO NOT COMPROMISE</h3>
  <p>Find an educated, licensed, experienced professional that you can relate to. Think about what it costs to get your best and the importance reaching this issue can have on your life.</p>
</main>

<aside class="sidebar">
  <div class="portrait" role="img" aria-label="Portrait photo of the psychologist"></div>
  <div class="side-inner">
    <div class="side-title">CLINICAL PSYCHOLOGIST</div>
    <div class="side-sub">California #PSY 6817</div>
    <div class="side-rule"></div>
    <ul class="side-list">
      <li>Doctoral Degree in Clinical Psychology</li>
      <li>Master's Degree in Counseling Psychology</li>
      <li>Doctoral Internship, Coastline Medical Center</li>
      <li>Master's Internship, Westmere Clinic</li>
    </ul>
    <div class="side-head">EXPERTISE</div>
    <div class="side-rule"></div>
    <ul class="side-list">
      <li>Dating &amp; Marriage</li>
      <li>Parenting &amp; Professional Relationships</li>
      <li>Depression &amp; Anxiety Issues</li>
      <li>Personality Disorders</li>
      <li>Life Management</li>
    </ul>
    <div class="side-head">SERVICES</div>
    <div class="side-rule"></div>
    <ul class="side-list">
      <li>Individual &amp; Group Counseling</li>
      <li>Couples / Family Therapy</li>
      <li>Stress Management</li>
      <li>Psychological Testing</li>
    </ul>
  </div>
</aside>

<section class="testimonial">
  <div class="avatar" role="img" aria-label="Small photo of a former patient"></div>
  <p class="quote">"I have had other counseling experiences; however, I have never made such significant strides until I saw Dr. Kalvoric. I like to persuade to relax, heart first. She is a true professional who is both compassionate and incredibly effective. Wonderful person. He has found my life is much better."</p>
  <p class="quote-by">— Mr. R., Lakeview</p>
</section>

<section class="col videos">
  <h4>VIDEOS</h4><div class="rule"></div>
  <div class="video-frame" role="img" aria-label="Video still titled Talk with Mara featuring the psychologist"><div class="video-bar"></div></div>
</section>

<section class="col contact">
  <h4>GET IN TOUCH</h4><div class="rule"></div>
  <div class="field">Name</div>
  <div class="field">Email</div>
  <div class="field">Phone</div>
  <div class="field message">Message</div>
  <span class="send">SEND</span>
</section>

<section class="col conversations">
  <h4>CONVERSATIONS</h4><div class="rule"></div>
  <div class="radio-art" role="img" aria-label="Silver Cedar Tunes radio spots cover art"></div>
</section>

<footer class="site-footer">
  <div class="badge-group">
    <div class="badge">Expert listed on<div class="badge-shape"></div></div>
    <div class="badge">Read Reviews on Rivo<div class="badge-shape red"></div></div>
  </div>
  <div class="map" role="img" aria-label="Map showing the office location"></div>
  <div class="reach">
    <div class="socials">
      <span class="social"><span class="social-dot"></span>Friendora</span>
      <span class="social"><span class="social-dot"></span>Linkvale</span>
    </div>
    <div class="phone">
      <svg width="12" height="12" viewBox="0 0 24 24" aria-hidden="true"><path fill="#2a8fa3" d="M6.6 10.8a15 15 0 006.6 6.6l2.2-2.2a1 1 0 011-.25 11.4 11.4 0 003.6.57 1 1 0 011 1V20a1 1 0 01-1 1A17 17 0 013 4a1 1 0 011-1h3.5a1 1 0 011 1c0 1.25.2 2.45.57 3.6a1 1 0 01-.25 1z"/></svg>
      949.555.0142
    </div>
    <div class="address">2210 Harbor Crest Dr, Suite 140<br>Seabright, CA 92600<br>info@drkalvoric.com</div>
  </div>
</footer>

<div class="copyright">© Dr. Mara L. Kalvoric 2018 All Rights Reserved · www.drkalvoric.com</div>
</body>
</html>
```